Brightfern Care Alliance Flirvo Ads

We want an ad created for the gay dating app flirvo. The size is 300x250. We want the ad to be sexy, with a shirtless man. We are advertising our free HIV and PrEP services. We are open to slogans about maybe "Bringing HIV and PrEP To You"
"Free PrEP and HIV Management"
Open to ideas.

We also offer through the Cedarline Relief Fund
Copay Assistance, Insurance Premium Assistance, Free Medical Services, etc
Our website is bfcanj.org

I do want the ad to have a Book Now Button

Gay sexually active males

```html
<!DOCTYPE html>
<html lang="en">
<head>
<meta charset="utf-8">
<title>Brightfern Care Alliance – Free PrEP &amp; HIV Management</title>
<link rel="stylesheet" href="https://fonts.googleapis.com/css2?family=Montserrat:wght@500;700;800;900&family=Bebas+Neue&display=swap">
<style>
  :root{
    --blue:#1e96ff;
    --indigo:#3b44e0;
    --pink:#f24bd8;
    --orange:#ff6a35;
    --ink:#000;
    --paper:#fff;
    --skin-light:#d9a07a;
    --skin-dark:#8a5a3c;
    --shorts:#5f6b74;
    --brand-gradient:linear-gradient(90deg,var(--blue) 0%,var(--indigo) 30%,var(--pink) 68%,var(--orange) 100%);
  }
  *{margin:0;padding:0;box-sizing:border-box}
  html,body{width:1200px;height:1034px;overflow:hidden;background:var(--paper)}
  .ad{position:relative;width:1200px;height:1034px;background:var(--paper);font-family:"Montserrat",sans-serif;overflow:hidden}
  .ad-shapes,.cta-shapes{position:absolute;inset:0}
  .photo-slot{position:absolute;left:720px;top:40px;width:455px;height:826px;
    background:linear-gradient(180deg,var(--skin-light) 0%,var(--skin-dark) 70%,var(--shorts) 100%);
    border-radius:200px 200px 30px 30px;opacity:.9}
  .headline-free{position:absolute;left:58px;top:6px;font-weight:900;font-size:238px;letter-spacing:-4px;line-height:1;
    background:var(--brand-gradient);-webkit-background-clip:text;background-clip:text;color:transparent}
  .headline-band{position:absolute;left:60px;top:250px;font-weight:800;font-size:112px;color:var(--paper);line-height:1;letter-spacing:-2px}
  .headline-management{position:absolute;left:60px;top:378px;font-weight:800;font-size:76px;color:var(--ink);line-height:1;letter-spacing:1px}
  .fund-intro{position:absolute;left:68px;top:470px;font-weight:500;font-size:34px;color:var(--ink);line-height:1}
  .fund-name{position:absolute;left:64px;top:509px;font-weight:500;font-size:49px;line-height:1.05;
    background:var(--brand-gradient);-webkit-background-clip:text;background-clip:text;color:transparent}
  .service-label{position:absolute;width:260px;text-align:center;font-family:"Bebas Neue",sans-serif;font-size:40px;line-height:36px;color:var(--ink)}
  .label-copay{left:6px;top:767px}
  .label-premium{left:242px;top:767px}
  .label-medical{left:480px;top:767px}
  .brand{position:absolute;left:72px;top:920px;display:flex;align-items:center;gap:16px}
  .brand-dot{width:76px;height:76px;border-radius:50%;background:var(--indigo)}
  .brand-name{font-weight:800;font-size:28px;line-height:32px;color:var(--indigo);width:220px}
  .contact{position:absolute;left:402px;display:flex;align-items:center;gap:12px;font-weight:700;color:var(--ink)}
  .contact-web{top:902px;font-size:40px}
  .contact-phone{top:952px;font-size:46px}
  .contact svg{flex:none}
  .book-word{position:absolute;left:845px;top:758px;width:268px;height:75px;background:var(--ink);color:var(--paper);
    font-weight:700;font-size:70px;line-height:75px;text-align:center;letter-spacing:2px}
  .now-word{position:absolute;left:800px;top:835px;width:360px;text-align:center;font-weight:900;font-size:104px;line-height:1;color:var(--paper)}
</style>
</head>
<body>
<main class="ad">
  <svg class="ad-shapes" width="1200" height="1034" viewBox="0 0 1200 1034" aria-hidden="true">
    <defs>
      <linearGradient id="brand" x1="0" x2="1" y1="0" y2="0">
        <stop offset="0" stop-color="#1e96ff"/>
        <stop offset=".3" stop-color="#3b44e0"/>
        <stop offset=".68" stop-color="#f24bd8"/>
        <stop offset="1" stop-color="#ff6a35"/>
      </linearGradient>
      <linearGradient id="ring-blue" x1="0" y1="0" x2="1" y2="1"><stop offset="0" stop-color="#1e7bff"/><stop offset="1" stop-color="#2b3fd0"/></linearGradient>
      <linearGradient id="ring-purple" x1="0" y1="0" x2="1" y2="1"><stop offset="0" stop-color="#b34be6"/><stop offset="1" stop-color="#6a35d8"/></linearGradient>
      <linearGradient id="ring-red" x1="0" y1="0" x2="1" y2="1"><stop offset="0" stop-color="#f2456a"/><stop offset="1" stop-color="#ff6a35"/></linearGradient>
    </defs>
    <polygon class="dark-panel" points="830,0 1200,0 1200,866 691,866" fill="#000"/>
    <polygon class="headline-band-shape" points="0,238 717,238 668,362 0,362" fill="url(#brand)"/>

    <polyline class="connector" points="52,486 14,486 14,661 48,661" fill="none" stroke="#3b44e0" stroke-width="2"/>
    <circle cx="55" cy="486" r="5" fill="#f24bd8"/>
    <line x1="206" y1="661" x2="285" y2="661" stroke="#5a3fe0" stroke-width="2"/>
    <line x1="443" y1="661" x2="522" y2="661" stroke="#e64bc0" stroke-width="2"/>

    <g class="service-copay">
      <circle cx="136" cy="661" r="88" fill="none" stroke="#1e7bff" stroke-width="1" opacity=".5"/>
      <circle cx="136" cy="661" r="70" fill="url(#ring-blue)"/>
      <circle cx="136" cy="661" r="56" fill="#fff"/>
      <g fill="none" stroke="#2b6cf0" stroke-width="3">
        <circle cx="136" cy="638" r="11"/><path d="M136 632v12M130 638h12"/>
        <circle cx="114" cy="660" r="6"/><circle cx="158" cy="660" r="6"/>
        <path d="M104 680c0-10 20-10 20 0M148 680c0-10 20-10 20 0M108 684h56"/>
      </g>
    </g>
    <g class="service-premium">
      <circle cx="373" cy="661" r="88" fill="none" stroke="#9b4be6" stroke-width="1" opacity=".5"/>
      <circle cx="373" cy="661" r="70" fill="url(#ring-purple)"/>
      <circle cx="373" cy="661" r="56" fill="#fff"/>
      <g fill="none" stroke="#e64bc0" stroke-width="3">
        <path d="M373 668c-22-14-26-34-12-38 6-2 10 2 12 6 2-4 6-8 12-6 14 4 10 24-12 38z"/>
        <path d="M348 650h12l5-8 6 14 5-6h22"/>
        <path d="M352 676l14 10h22l10-8M352 676v14"/>
      </g>
    </g>
    <g class="service-medical">
      <circle cx="610" cy="661" r="88" fill="none" stroke="#f2456a" stroke-width="1" opacity=".5"/>
      <circle cx="610" cy="661" r="70" fill="url(#ring-red)"/>
      <circle cx="610" cy="661" r="56" fill="#fff"/>
      <g fill="none" stroke="#f2456a" stroke-width="3">
        <circle cx="610" cy="632" r="8"/>
        <rect x="594" y="644" width="32" height="40"/>
        <rect x="578" y="656" width="16" height="28"/><rect x="626" y="656" width="16" height="28"/>
        <path d="M610 650v14M603 657h14M604 684v-12h12v12"/>
      </g>
    </g>

    <rect class="footer-divider" x="0" y="866" width="1200" height="14" fill="url(#brand)"/>
    <rect x="0" y="880" width="1200" height="154" fill="#fff"/>
  </svg>

  <div class="photo-slot" role="img" aria-label="Photo of a smiling shirtless man giving a thumbs up, wearing grey patterned shorts"></div>

  <svg class="cta-shapes" width="1200" height="1034" viewBox="0 0 1200 1034" aria-hidden="true">
    <defs>
      <linearGradient id="cta" x1="0" x2="1" y1="0" y2="0">
        <stop offset="0" stop-color="#1e96ff"/>
        <stop offset=".3" stop-color="#3b44e0"/>
        <stop offset=".68" stop-color="#f24bd8"/>
        <stop offset="1" stop-color="#ff6a35"/>
      </linearGradient>
    </defs>
    <polygon points="798,810 1166,810 1152,938 787,938" fill="url(#cta)"/>
    <polygon points="930,938 1030,938 980,994" fill="#f24bd8"/>
  </svg>

  <h1 class="headline-free">FREE</h1>
  <p class="headline-band">PrEP &amp; HIV</p>
  <p class="headline-management">MANAGEMENT</p>

  <p class="fund-intro">We also offer through the</p>
  <p class="fund-name">Cedarline Relief Fund</p>

  <p class="service-label label-copay">Copay<br>Assistance</p>
  <p class="service-label label-premium">Insurance Premium<br>Assistance</p>
  <p class="service-label label-medical">Free Medical<br>Services</p>

  <div class="brand">
    <span class="brand-dot"></span>
    <span class="brand-name">Brightfern Care Alliance</span>
  </div>

  <p class="contact contact-web">
    <svg width="38" height="38" viewBox="0 0 38 38" aria-hidden="true"><g fill="none" stroke="#3b44e0" stroke-width="3"><circle cx="19" cy="19" r="16"/><ellipse cx="19" cy="19" rx="7" ry="16"/><path d="M3 19h32M6 11h26M6 27h26"/></g></svg>
    www.bfcanj.org
  </p>
  <p class="contact contact-phone">
    <svg width="38" height="38" viewBox="0 0 38 38" aria-hidden="true"><path d="M9 4l7 8-4 4c2 5 6 9 11 11l4-4 8 7-4 5C19 35 3 19 4 8z" fill="none" stroke="#f2456a" stroke-width="3" stroke-linejoin="round"/></svg>
    201-555-0148
  </p>

  <p class="book-word">BOOK</p>
  <p class="now-word">NOW!</p>
</main>
</body>
</html>
```